Hvac and insulation company needs good looking business card design

We are hvac and insulation company and looking for a new business cards that look to today standards designs

Target Market(s)

homeowners

Industry/Entity Type

Hvac

Contact Information for Business Card

Name: Walter Brinoku
Home comfort consultant
address: 4827 Dunmore St #215 Oakland, CA 94619
office: 888-316-2790
cell: 510-742-3185
Lic.# 584261
Email: walter@corvane-hvac.com
Web: corvane-hvac.com

Requirements
Must have
• clean and sleek look
Nice to have
• simple with a clean look
Should not have
• to busy business card

```html
<!DOCTYPE html>
<html lang="en">
<head>
<meta charset="utf-8">
<title>Corvane business card</title>
<link rel="stylesheet" href="https://fonts.googleapis.com/css2?family=Work+Sans:wght@400;500;600&display=swap">
<style>
  :root {
    --bg: #3b3732;
    --orange: #f58220;
    --white: #ffffff;
    --ink: #555555;
  }
  * { margin: 0; padding: 0; box-sizing: border-box; }
  html, body { width: 1200px; height: 930px; overflow: hidden; }
  body {
    background: var(--bg);
    font-family: "Work Sans", Arial, sans-serif;
    position: relative;
  }
  .card {
    position: absolute;
    width: 700px;
    height: 400px;
    border-radius: 22px;
  }
  .card-front {
    left: 70px; top: 60px;
    background: var(--orange);
    color: var(--white);
  }
  .card-back {
    left: 430px; top: 470px;
    background: var(--white);
  }
  .brand {
    display: flex;
    align-items: center;
    gap: 14px;
    font-weight: 600;
    letter-spacing: -1px;
  }
  .brand-dot { border-radius: 50%; flex: none; }
  .card-front .brand {
    position: absolute; left: 0; right: 0; top: 140px;
    justify-content: center;
    font-size: 64px;
  }
  .card-front .brand-dot { width: 38px; height: 38px; background: var(--white); }
  .license {
    position: absolute; left: 0; right: 0; top: 300px;
    text-align: center;
    font-size: 18px;
    letter-spacing: 0.5px;
  }
  .card-back .brand {
    position: absolute; left: 60px; top: 110px;
    font-size: 48px;
    color: var(--orange);
  }
  .card-back .brand-dot { width: 30px; height: 30px; background: var(--orange); }
  .contact {
    position: absolute; left: 390px; top: 100px;
    color: var(--ink);
    font-size: 15px;
    line-height: 1.45;
  }
  .contact-name {
    color: var(--orange);
    font-size: 23px;
    font-weight: 500;
    text-transform: uppercase;
    line-height: 1.1;
  }
  .contact-title { font-size: 16px; margin-bottom: 10px; }
  .contact-address { margin-bottom: 10px; }
  .contact-list { list-style: none; }
  .contact-list li { display: flex; align-items: center; gap: 9px; }
  .contact-list svg { width: 12px; height: 12px; flex: none; fill: var(--orange); }
  .web-domain { color: var(--orange); }
</style>
</head>
<body>
  <section class="card card-front">
    <div class="brand"><span class="brand-dot"></span>corvane</div>
    <p class="license">Lic.# 584261</p>
  </section>

  <section class="card card-back">
    <div class="brand"><span class="brand-dot"></span>corvane</div>
    <div class="contact">
      <p class="contact-name">Walter Brinoku</p>
      <p class="contact-title">Home comfort consultant</p>
      <p class="contact-address">4827 Dunmore St<br>#215 Oakland, CA 94619</p>
      <ul class="contact-list">
        <li><svg viewBox="0 0 12 12" aria-hidden="true"><path d="M2.5 1 L4.5 1 L5.3 3.5 L4 4.5 Q5 7 7.5 8 L8.5 6.7 L11 7.5 L11 9.5 Q10.5 11 9 11 Q1 10 1 2.5 Q1 1 2.5 1Z"/></svg>888-316-2790</li>
        <li><svg viewBox="0 0 12 12" aria-hidden="true"><path d="M3 0.5 H9 V11.5 H3Z M4 1.5 V9 H8 V1.5Z"/></svg>510-742-3185</li>
        <li><svg viewBox="0 0 12 12" aria-hidden="true"><path d="M0.5 2.5 H11.5 V9.5 H0.5Z M1.8 3.5 L6 6.5 L10.2 3.5Z"/></svg>walter@corvane-hvac.com</li>
        <li><svg viewBox="0 0 12 12" aria-hidden="true"><circle cx="6" cy="6" r="5.5"/></svg>www.<span class="web-domain">corvane-hvac</span>.com</li>
      </ul>
    </div>
  </section>
</body>
</html>
```